BrightHarbor logo and website profile

BrightHarbor is a newly started business angel network investing in entrepreneurs and start-ups. We need a smart looking logo and website design (based on Wordpress).
The aim of the site is to attract 2 customer segments;
1) Entrepreneurs and start-ups looking for investors
2) Investors/ business angels looking to become part of a larger network of investors for better access to investments
A successful conversion on the website would be for the entrepreneur or investor sending us an e-mail to submit their investment proposal, inquire about our services or ask to join the network of investors.
The website should focus on presenting Bright Harbor and our offerings towards the 2 customer segments. This is NOT a platform like e.g. fundly.example.
Sites we like;
http://demo.quilvex.example/themes/orchid/agency/
http://www.trellisadvisory.example (it's a bit bleak - needs a little more color)
Hi all,
Target Market(s)
Two target markets; 1) entrepreneurs looking for investors 2) business angels looking for investment opportunities
Industry/Entity Type
Investment
Requirements
Must have
- The keywords we want associated with our brand are;
Innovation – Integrity – Knowledgeable – Growth – Entrepreneurship
Logodesign (symbol and smart presentation of the company name - bright harbor, both with and without .com)
Wordpress design, pages we need:
- landing page with clear CTA for entrepreneurs and clear CTA for investors
- Portfolio overview of investments made
- General page for our approach, services etc
- Contact us page
- Favicon
- News
- Header/footer information
Other functionality we need;
- Social media integration
The design must support mobile and iPads as well.
We like: less is more :)

```html
<!DOCTYPE html>
<html lang="en">
<head>
<meta charset="utf-8">
<title>Bright Harbor</title>
<link rel="stylesheet" href="https://fonts.googleapis.com/css2?family=Oswald:wght@400;500;700&family=Open+Sans:ital,wght@0,400;1,400&family=PT+Sans&display=swap">
<style>
  :root {
    --ink: #333333;
    --heading: #4a4a4a;
    --sub: #8a8a8a;
    --body: #666666;
    --black: #000000;
    --white: #ffffff;
    --page: #ebebeb;
    --band: #d6d6d6;
    --red: #e0141f;
    --footer-base: #c9c9c9;
    --social: #8f8f8f;
    --social-panel: #d4d4d4;
  }
  * { margin: 0; padding: 0; box-sizing: border-box; }
  html, body { width: 1126px; height: 1200px; overflow: hidden; }
  body { position: relative; background: var(--page); font-family: Arial, Helvetica, sans-serif; }

  .site-header { position: absolute; left: 0; top: 0; width: 1126px; height: 80px; background: var(--white); }
  .brand { position: absolute; left: 14px; top: 22px; display: flex; align-items: center; gap: 10px; }
  .brand-mark { width: 26px; height: 26px; background: var(--red); }
  .brand-name { font-family: "Oswald", sans-serif; font-weight: 700; font-size: 31px; color: var(--ink); letter-spacing: 0.5px; line-height: 1; }
  .header-contact { position: absolute; right: 10px; top: 12px; text-align: right; font-family: "Oswald", sans-serif; color: #555; line-height: 1; }
  .header-contact .label { font-size: 18px; font-weight: 500; }
  .header-contact .phone { font-size: 31px; font-weight: 500; margin-top: 4px; }

  .main-nav { position: absolute; left: 0; top: 80px; width: 1126px; height: 45px; background: var(--black); }
  .main-nav ul { list-style: none; display: flex; position: absolute; left: 198px; top: 12px; gap: 48px; }
  .main-nav a { color: var(--white); text-decoration: none; font-family: "Open Sans", sans-serif; font-style: italic; font-size: 16px; }

  .hero { position: absolute; left: 0; top: 125px; width: 1126px; height: 500px; }

  .audience { position: absolute; top: 692px; width: 440px; }
  .audience-investors { left: 20px; }
  .audience-founders { left: 532px; }
  .audience h2 { font-family: "Oswald", sans-serif; font-weight: 500; font-size: 31px; color: var(--heading); line-height: 1; letter-spacing: -0.3px; text-transform: uppercase; padding-left: 16px; }
  .audience-founders h2 { padding-left: 0; }
  .audience .tagline { font-family: "Oswald", sans-serif; font-size: 16px; color: var(--sub); text-align: right; margin-top: 1px; padding-right: 0; width: 420px; letter-spacing: -0.2px; }
  .audience-founders .tagline { width: 418px; }
  .audience p { font-size: 14px; color: var(--body); line-height: 17px; margin-top: 26px; width: 410px; padding-left: 9px; }
  .audience-founders p { padding-left: 1px; }
  .cta { display: flex; align-items: center; gap: 12px; margin-top: 36px; font-size: 13px; color: #111; line-height: 15px; }
  .audience-founders .cta { margin-top: 22px; }

  .social { position: absolute; left: 1020px; top: 654px; width: 81px; height: 340px; background: var(--social-panel); border-radius: 5px; }
  .social a { position: absolute; left: 15px; width: 50px; height: 50px; border-radius: 9px; background: var(--social); box-shadow: inset 0 -3px 0 rgba(0,0,0,0.12); }

  .site-footer { position: absolute; left: 0; top: 1101px; width: 1126px; height: 99px; }
  .footer-nav { height: 46px; background: var(--black); display: flex; justify-content: center; align-items: center; gap: 12px; padding-left: 10px; }
  .footer-nav a { color: var(--white); text-decoration: none; font-size: 14px; }
  .footer-nav .dot { color: #aaa; font-size: 12px; }
  .copyright { height: 53px; background: var(--footer-base); text-align: center; font-family: "PT Sans", sans-serif; font-size: 13px; color: #111; padding-top: 16px; }
</style>
</head>
<body>
  <header class="site-header">
    <div class="brand">
      <span class="brand-mark"></span>
      <span class="brand-name">BRIGHT HARBOR</span>
    </div>
    <div class="header-contact">
      <div class="label">CONTACT</div>
      <div class="phone">02-555-01936</div>
    </div>
  </header>

  <nav class="main-nav">
    <ul>
      <li><a href="#">HOME</a></li>
      <li><a href="#">PORTFOLIO</a></li>
      <li><a href="#">APPROACH AND SERVICES</a></li>
      <li><a href="#">NEWS</a></li>
      <li><a href="#">CONTACT US</a></li>
    </ul>
  </nav>

  <svg class="hero" viewBox="0 0 1126 500" width="1126" height="500">
    <defs>
      <linearGradient id="steel" x1="0" y1="0" x2="1" y2="1">
        <stop offset="0" stop-color="#b5b5b5"/>
        <stop offset="0.5" stop-color="#6e6e6e"/>
        <stop offset="1" stop-color="#a8a8a8"/>
      </linearGradient>
      <linearGradient id="advisor" x1="0" y1="0" x2="1" y2="1">
        <stop offset="0" stop-color="#e4e8ec"/>
        <stop offset="0.55" stop-color="#b8bcc0"/>
        <stop offset="1" stop-color="#6f7276"/>
      </linearGradient>
      <linearGradient id="partner" x1="0" y1="0" x2="1" y2="1">
        <stop offset="0" stop-color="#7fa9c8"/>
        <stop offset="0.5" stop-color="#c9dcea"/>
        <stop offset="1" stop-color="#eef2f5"/>
      </linearGradient>
    </defs>
    <g role="img" aria-label="Grey steel structure backdrop with red lower band">
      <rect x="0" y="0" width="1126" height="461" fill="url(#steel)"/>
      <rect x="0" y="384" width="1126" height="77" fill="var(--red)"/>
    </g>
    <polygon points="184,6 630,6 486,489 43,489" fill="var(--white)"/>
    <polygon points="196,20 612,20 476,475 60,475" fill="url(#advisor)" role="img" aria-label="Photo of a smiling businessman in a grey suit and glasses"/>
    <polygon points="666,6 1112,6 969,489 525,489" fill="var(--white)"/>
    <polygon points="680,20 1092,20 960,477 538,477" fill="url(#partner)" role="img" aria-label="Photo of a businesswoman holding a pen with a colleague behind her"/>
  </svg>

  <section class="audience audience-investors">
    <h2>Investors / Business Angels</h2>
    <div class="tagline">looking for better access to investments</div>
    <p>Are you wondering where to invest your money and looking for a successfull ROI? You just came to the right place, we can help you decide and find a good business investment the you desire.</p>
    <div class="cta">
      <svg width="32" height="34" viewBox="0 0 32 34" aria-hidden="true">
        <circle cx="16" cy="17" r="15" fill="#dcdcdc"/>
        <rect x="6" y="12" width="20" height="13" fill="#f5f5f5" stroke="#888"/>
        <polyline points="6,12 16,20 26,12" fill="none" stroke="#888"/>
      </svg>
      <span>contact us and get a business proposal or<br>submit invsestment proposal</span>
    </div>
  </section>

  <section class="audience audience-founders">
    <h2>Entrepreneurs and Startups</h2>
    <div class="tagline">looking for investors</div>
    <p>Have a business in mind but don't have enought funds to continue with the venture? This is the right place to take your business into a higher next and look for investors to help you achive the business of your dreams.</p>
    <div class="cta">
      <svg width="32" height="34" viewBox="0 0 32 34" aria-hidden="true">
        <circle cx="16" cy="17" r="15" fill="#dcdcdc"/>
        <rect x="6" y="12" width="20" height="13" fill="#f5f5f5" stroke="#888"/>
        <polyline points="6,12 16,20 26,12" fill="none" stroke="#888"/>
      </svg>
      <span>contact us and submit your business proposal</span>
    </div>
  </section>

  <aside class="social" aria-label="Social links">
    <a href="#" style="top:13px" aria-label="Social profile 1"></a>
    <a href="#" style="top:78px" aria-label="Social profile 2"></a>
    <a href="#" style="top:142px" aria-label="Social profile 3"></a>
    <a href="#" style="top:208px" aria-label="Social profile 4"></a>
    <a href="#" style="top:274px" aria-label="Feed"></a>
  </aside>

  <footer class="site-footer">
    <nav class="footer-nav">
      <a href="#">HOME</a><span class="dot">·</span>
      <a href="#">PORTFOLIO</a><span class="dot">·</span>
      <a href="#">APPROACH AND SERVICES</a><span class="dot">·</span>
      <a href="#">NEWS</a><span class="dot">·</span>
      <a href="#">CONTACT US</a>
    </nav>
    <div class="copyright">© Copyright 2013 BRIGHT HARBOR All Rights Reserved.</div>
  </footer>
</body>
</html>
```